Quorva - corporate Business Card

We need a good look and innovative business card for a new start up company based in Los Angeles called "Quorva". We are in a payment business, including payment card, app, and ewallet. We are expert in online payment and Card not present (CNP) transaction.
We need an innovative, modern business card.

Our logo font is Aero Matics

Target Market(s)

Startup - Bank - Online Payment - Card Manufacturing

Industry/Entity Type

Startup

Contact Information for Business Card

phone: 555 014 7396 - Address: 4172 Marlowe blvd, Harlow Park, CA 90299

Requirements
Must have
• Message: innovative, professional, expert, high tech, trust, online payment expert, security
Nice to have
• no comment
Should not have
• no Comment

```html
<!DOCTYPE html>
<html lang="en">
<head>
<meta charset="utf-8">
<title>Quorva – Business Card</title>
<link rel="stylesheet" href="https://fonts.googleapis.com/css2?family=Libre+Franklin:wght@400;500;600&display=swap">
<style>
  :root {
    --page: #3a3330;
    --card: #141415;
    --card-back: #111112;
    --red: #d3202e;
    --white: #f2f2f2;
    --grey: #8d8d8f;
    --emboss: #2a2a2c;
  }
  * { box-sizing: border-box; margin: 0; padding: 0; }
  html, body { width: 1200px; height: 864px; overflow: hidden; }
  body {
    background: var(--page);
    font-family: "Libre Franklin", Arial, sans-serif;
    position: relative;
  }
  .card {
    position: absolute;
    top: 283px;
    width: 520px;
    height: 298px;
    border-radius: 3px;
    box-shadow: 0 12px 30px rgba(0,0,0,.45);
    overflow: hidden;
  }
  .card--back { left: 60px; background: var(--card-back); }
  .card--front { left: 620px; background: var(--card); }

  /* back side */
  .back-mark {
    position: absolute;
    left: 50%; top: 66px;
    width: 132px; height: 132px;
    margin-left: -66px;
    border-radius: 50%;
    background: radial-gradient(circle at 40% 30%, #3a3a3c, var(--emboss) 70%);
  }
  .back-web {
    position: absolute;
    left: 0; right: 0; top: 226px;
    text-align: center;
    color: var(--grey);
    font-size: 12px;
    letter-spacing: 5px;
  }

  /* front side */
  .brand {
    position: absolute;
    right: 34px; top: 50px;
    display: flex; align-items: center; gap: 10px;
  }
  .brand-dot {
    width: 50px; height: 50px; border-radius: 50%;
    background: var(--red);
  }
  .brand-name {
    color: var(--red);
    font-size: 42px;
    font-weight: 500;
    letter-spacing: 1px;
  }
  .person { position: absolute; left: 26px; top: 96px; }
  .person-name { color: var(--red); font-size: 16px; line-height: 18px; }
  .person-title { color: var(--white); font-size: 14px; line-height: 18px; }
  .contacts {
    position: absolute; left: 26px; top: 140px;
    list-style: none;
    color: var(--white); font-size: 12.5px;
  }
  .contacts li { display: flex; align-items: center; gap: 8px; line-height: 20px; }
  .contacts svg { width: 11px; height: 11px; fill: var(--red); }
  .rule { position: absolute; left: 0; top: 0; }
  .address {
    position: absolute; right: 40px; top: 240px;
    color: var(--white); font-size: 14px; line-height: 19px;
  }
</style>
</head>
<body>
  <section class="card card--back" aria-label="Card back">
    <div class="back-mark"></div>
    <p class="back-web">www.quorva.com</p>
  </section>

  <section class="card card--front" aria-label="Card front">
    <div class="brand">
      <span class="brand-dot"></span>
      <span class="brand-name">Quorva</span>
    </div>

    <div class="person">
      <p class="person-name">Mara Venn</p>
      <p class="person-title">President</p>
    </div>

    <svg class="rule" width="520" height="298" aria-hidden="true">
      <line x1="94" y1="129" x2="490" y2="232" stroke="#f2f2f2" stroke-width="1.2"/>
    </svg>

    <ul class="contacts">
      <li><svg viewBox="0 0 12 12"><path d="M2 1h3l1 3-1.5 1a6 6 0 0 0 2.5 2.5L8 6l3 1v3a1 1 0 0 1-1 1A9 9 0 0 1 1 2a1 1 0 0 1 1-1z"/></svg>555 014 7396</li>
      <li><svg viewBox="0 0 12 12"><path d="M1 3h10v6H1z M1 3l5 3.5L11 3" fill="none" stroke="#d3202e" stroke-width="1.4"/></svg>mara@quorva.com</li>
      <li><svg viewBox="0 0 12 12"><circle cx="6" cy="6" r="5"/><path d="M1 6h10M6 1c2 2 2 8 0 10M6 1c-2 2-2 8 0 10" stroke="#141415" stroke-width=".9" fill="none"/></svg>www.quorva.com</li>
    </ul>

    <p class="address">4172 Marlowe blvd<br>Harlow Park, CA 90299</p>
  </section>
</body>
</html>
```